Personal Injury Law Firm needs folder design

Need a folder design for our personal injury law firm, Corrow & Talmidge, LLC. to give to all of our clients with their documents at the end of their case. I've attached our branding guide. We are branded as the 5 star law firm that fights for our clients like family. It should incorporate our colors or Green and White. We'd like to convey a message of moving on to the next chapter after finishing their case.

```html
<!DOCTYPE html>
<html lang="en">
<head>
<meta charset="utf-8">
<title>Corrow &amp; Talmidge, LLC. – Client Folder</title>
<link href="https://fonts.googleapis.com/css2?family=Open+Sans:wght@400;600;700;800&display=swap" rel="stylesheet">
<style>
  :root {
    --green: #05a27a;
    --brand-green: #13996f;
    --spine: #1c3338;
    --ink: #1d3a3a;
    --accent-yellow: #f6e000;
    --white: #ffffff;
    --stage: #ffffff;
  }
  * { box-sizing: border-box; margin: 0; padding: 0; }
  html, body {
    width: 1200px; height: 2203px; overflow: hidden;
    background: var(--stage);
    font-family: "Open Sans", Arial, sans-serif;
  }
  .folder {
    position: absolute; left: 60px; top: 621px;
    width: 1080px; height: 960px;
    filter: drop-shadow(0 6px 14px rgba(0,0,0,0.18));
  }
  .panel { position: absolute; }
  .spine { left: 468px; top: 7px; width: 117px; height: 700px; background: var(--spine); }
  .panel-white { background: var(--white); height: 348px; top: 12px; }
  .panel-white.left { left: 17px; width: 451px; }
  .panel-white.right { left: 585px; width: 453px; }
  .panel-green { background: var(--green); top: 360px; height: 345px; }
  .panel-green.left { left: 35px; width: 433px; }
  .panel-green.right { left: 585px; width: 453px; }

  .pockets { position: absolute; left: 0; top: 0; width: 1080px; height: 960px; }

  .brand {
    position: absolute; display: flex; align-items: center; gap: 12px;
    transform: translateX(-50%);
  }
  .brand-square { width: 70px; height: 60px; background: var(--brand-green); }
  .brand-name {
    font-size: 20px; font-weight: 600; color: var(--brand-green);
    letter-spacing: 0.5px; white-space: nowrap; text-transform: uppercase;
  }
  .brand.flipped { transform: translateX(-50%) rotate(180deg); }
  .brand.flipped .brand-square { background: var(--white); width: 76px; height: 64px; }
  .brand.flipped .brand-name { color: var(--white); }

  .photo {
    position: absolute; top: 160px; width: 432px; height: 280px;
    border: 5px solid var(--white);
  }
  .photo.team { left: 73px; background: linear-gradient(180deg, #cfe3dc 0%, #8fb3a7 45%, #2a2f33 100%); }
  .photo.handshake { left: 567px; background: linear-gradient(135deg, #e9e6df 0%, #f6f4ef 40%, #9a9a98 75%, #3a3b3e 100%); }

  .contact {
    position: absolute; left: 35px; width: 433px; top: 480px;
    text-align: center; color: var(--white);
  }
  .contact .icon { display: block; margin: 0 auto; }
  .contact .hours { color: var(--accent-yellow); font-weight: 700; font-size: 20px; margin-top: 2px; }
  .contact .phone { font-weight: 700; font-size: 29px; line-height: 1.2; margin-bottom: 4px; }
  .contact .address { font-size: 13px; line-height: 17px; margin-top: 4px; }

  .web {
    position: absolute; top: 652px; text-align: center;
    font-size: 13px; letter-spacing: 2.6px; color: var(--white); font-weight: 600;
  }
  .web.left { left: 35px; width: 433px; }
  .web.right { left: 585px; width: 453px; }

  .cover-text { position: absolute; left: 585px; width: 453px; top: 490px; text-align: center; }
  .cover-text .kicker { font-size: 26px; font-weight: 700; color: var(--ink); }
  .cover-text .headline {
    margin-top: 22px; font-size: 41px; font-weight: 800; color: var(--white);
    line-height: 40px; letter-spacing: 1px;
  }
</style>
</head>
<body>
  <main class="folder">
    <div class="panel spine"></div>
    <div class="panel panel-white left"></div>
    <div class="panel panel-green left"></div>
    <div class="panel panel-white right"></div>
    <div class="panel panel-green right"></div>

    <div class="brand" style="left:252px; top:60px;">
      <div class="brand-square"></div>
      <span class="brand-name">Corrow &amp; Talmidge, LLC.</span>
    </div>
    <div class="brand" style="left:812px; top:57px;">
      <div class="brand-square"></div>
      <span class="brand-name">Corrow &amp; Talmidge, LLC.</span>
    </div>

    <div class="photo team" role="img" aria-label="Group portrait of the firm's five attorneys"></div>
    <div class="photo handshake" role="img" aria-label="Handshake over a desk with scales of justice and a gavel"></div>

    <section class="contact">
      <svg class="icon" width="22" height="22" viewBox="0 0 22 22" aria-hidden="true">
        <circle cx="11" cy="11" r="11" fill="var(--spine)"/>
        <path d="M7.5 6.5c.6-.6 1.3-.5 1.7.1l1 1.5c.3.5.2 1-.2 1.4l-.6.6c.5 1.1 1.4 2 2.5 2.5l.6-.6c.4-.4.9-.5 1.4-.2l1.5 1c.6.4.7 1.1.1 1.7l-.7.7c-.8.8-2.6.4-4.6-1.6S6 8 6.8 7.2z" fill="var(--white)"/>
      </svg>
      <p class="hours">Call Or Text 24-7</p>
      <p class="phone">(555) 014-2287</p>
      <svg class="icon" width="22" height="22" viewBox="0 0 22 22" aria-hidden="true">
        <circle cx="11" cy="11" r="11" fill="var(--spine)"/>
        <path d="M11 5a4 4 0 0 0-4 4c0 3 4 7 4 7s4-4 4-7a4 4 0 0 0-4-4zm0 5.5a1.5 1.5 0 1 1 0-3 1.5 1.5 0 0 1 0 3z" fill="var(--white)"/>
      </svg>
      <p class="address">4180 Harbor Crest Lane<br>Palm Vista, FL 33000</p>
    </section>
    <p class="web left">www.corrowandtalmidge.com</p>

    <section class="cover-text">
      <h2 class="kicker">PERSONAL INJURY LAW FIRM</h2>
      <h1 class="headline">FIGHTING FOR<br>YOU LIKE FAMILY</h1>
    </section>
    <p class="web right">www.corrowandtalmidge.com</p>

    <svg class="pockets" viewBox="0 0 1080 960" aria-hidden="true">
      <polygon points="35,705 2,718 2,925 35,935" fill="var(--green)"/>
      <polygon points="35,705 530,705 500,935 35,935" fill="var(--spine)"/>
      <polygon points="1038,705 1073,718 1073,925 1038,935" fill="var(--green)"/>
      <polygon points="545,705 1038,705 1038,935 578,935" fill="var(--spine)"/>
    </svg>

    <div class="brand flipped" style="left:290px; top:793px;">
      <div class="brand-square"></div>
      <span class="brand-name">Corrow &amp; Talmidge, LLC.</span>
    </div>
    <div class="brand flipped" style="left:823px; top:793px;">
      <div class="brand-square"></div>
      <span class="brand-name">Corrow &amp; Talmidge, LLC.</span>
    </div>
  </main>
</body>
</html>
```